a customWebsite for our live Escape room with landing page and then links to the multiple locations

We are looking for a new main landing page that then goes to the location site So puzzlevaultery.com (main landing page)
The site needs to have main company info locations to choose a countdown clock and book now option news articles and video, a link to social media.
a link to the locations
the locations page will go to puzzlevaulterydm.com or puzzlevaulterymke.com for the des moines location and the milwaukee location with more locations opening soon. The location pages need to have a one page theme with book now options and social media links. We are a escape room company please visit puzzlevaulterydm.com to get a idea of what we are looking for. We want to work with someone that can also do updates as we add new rooms etc.. Also must be able to design and upload the site to godaddy for us. We would like the countdown timer to display a message at the end (promo code etc) All pages need to link back to the main page and the Des moines Location needs to link to qrtdesmoines.com. We are looking for a interactive responsive site that shows what we are. The room bios for the MKE location will be upfoaded soon the rooms for des moines are on puzzlevaulterydm.com. please google escape rooms and visit competitor sites to help get more ideas we are open to color changes or logo changes we just shared a video and article on facebook to help http://www.prairiegazette-news.com/story/entertainment/2015/02/19/puzzle-vaultery-des-moines/58214706/

Reason: Not one design has had a landing page with the links to the locations etc....

Reason: Still looking for a main page for puzzle vaultery on the main landing page stuff about escape games news stories who should try also a video feed and countdown timmer then a link to des moines and Milwaukee location on the milwaukee page info on the location and the rooms with a book now option. on the des moines location info on the location and rooms with a book now location pages should have links to facebook twitter for that location

Target Market(s)

Customers looking for information about our escape rooms

Industry/Entity Type

It Company

Number of Pages Required

4 page

Requirements
Must have
• main landing page, Des Moines Location Page, Milwaukee Location Page
• booking page
Nice to have
• Be creative look at our page and other pages related to escape rooms to get ideas

```html
<!DOCTYPE html>
<html lang="en">
<head>
<meta charset="utf-8">
<title>Puzzle Vaultery Des Moines</title>
<link rel="stylesheet" href="https://fonts.googleapis.com/css2?family=Oswald:wght@400;500;600&family=Open+Sans:wght@400;600;700&display=swap">
<style>
:root{
  --yellow:#f8c21c;
  --orange:#e79a1f;
  --ink:#2b2b2b;
  --muted:#6f6f6f;
  --dark:#1c1c1c;
  --darker:#151515;
  --line:#e3e3e3;
  --panel:#f1f1f1;
  --white:#ffffff;
}
*{box-sizing:border-box;margin:0;padding:0}
html,body{width:1200px;height:2468px;overflow:hidden;background:var(--white)}
body{font-family:"Open Sans",Arial,sans-serif;color:var(--ink);font-size:13px;position:relative}
.wrap{width:1000px;margin:0 auto;position:relative}

.site-header{height:112px;background:linear-gradient(#262626,#161616);display:flex;align-items:center;justify-content:center}
.brand{display:flex;align-items:center;gap:14px}
.brand-mark{width:40px;height:40px;background:var(--yellow)}
.brand-name{font-family:"Oswald",sans-serif;font-weight:500;color:var(--yellow);font-size:30px;letter-spacing:2px;line-height:1;text-transform:uppercase}
.main-nav{height:40px;background:#f4f4f4;border-bottom:1px solid var(--line)}
.main-nav ul{list-style:none;display:flex;height:40px;width:1000px;margin:0 auto;align-items:stretch}
.main-nav li{font-family:"Oswald",sans-serif;font-size:12px;letter-spacing:.5px;color:#555;display:flex;align-items:center;padding:0 16px;text-transform:uppercase}
.main-nav li.active{background:var(--yellow);color:var(--ink)}
.main-nav li.book{margin-left:auto;background:var(--yellow);color:var(--ink);font-weight:600}

.hero{height:420px;position:relative;background:#3a3a3a}
.hero-media{position:absolute;inset:0;background:radial-gradient(ellipse at 50% 45%,#6b6b6b 0%,#3e3e3e 45%,#202020 100%)}
.hero-arrow{position:absolute;top:190px;width:30px;height:40px;display:flex;align-items:center;justify-content:center}
.hero-arrow.left{left:20px}.hero-arrow.right{right:20px}

.welcome{height:300px;padding-top:36px}
.welcome .wrap{display:flex;justify-content:space-between}
.welcome-text{width:640px}
.section-title{font-family:"Oswald",sans-serif;font-weight:500;color:var(--orange);font-size:22px;margin-bottom:12px}
.welcome-text p{color:var(--muted);font-size:12px;line-height:20px;margin-bottom:12px}
.more{font-family:"Oswald",sans-serif;font-size:12px;color:var(--ink);font-weight:600}
.stat-box{width:310px;height:200px;border:1px solid var(--line);border-radius:4px;padding:16px;text-align:center}
.stat-box h3{font-family:"Oswald",sans-serif;font-weight:400;font-size:12px;color:var(--muted);letter-spacing:.5px;margin-bottom:14px;text-align:left}
.donuts{display:flex;justify-content:space-around}
.donut{position:relative;width:110px;height:110px}
.donut span{position:absolute;inset:0;display:flex;flex-direction:column;align-items:center;justify-content:center;font-family:"Oswald",sans-serif;font-size:26px;color:var(--ink);line-height:1}
.donut small{font-family:"Open Sans",sans-serif;font-size:9px;color:var(--muted);margin-top:4px}

.book-bar{width:1000px;height:58px;margin:0 auto;background:var(--yellow);display:flex;align-items:center;justify-content:center;font-family:"Oswald",sans-serif;font-size:24px;font-weight:500;color:#5a2a00;letter-spacing:1px}

.press{height:250px;padding-top:48px}
.press-head{display:flex;justify-content:space-between;align-items:center;border-bottom:1px solid var(--line);padding-bottom:8px;margin-bottom:20px}
.press-head .section-title{margin:0}
.press-nav{display:flex;gap:6px}
.press-nav i{width:16px;height:16px;background:#ddd;display:block}
.press-list{display:flex;justify-content:space-between}
.press-item{width:235px;display:flex;gap:12px}
.date{width:46px;height:46px;border-radius:50%;background:var(--yellow);flex:none;display:flex;flex-direction:column;align-items:center;justify-content:center;font-family:"Oswald",sans-serif;line-height:1;color:var(--ink)}
.date b{font-size:16px;font-weight:500}.date em{font-style:normal;font-size:9px}
.press-item h4{font-size:11px;font-weight:700;margin-bottom:4px}
.press-item p{font-size:10px;color:var(--muted);line-height:15px}

.rooms-head{height:44px;position:relative;margin-top:20px}
.rooms-head:before{content:"";position:absolute;left:100px;right:100px;top:22px;height:2px;background:var(--yellow)}
.rooms-head span{position:absolute;left:540px;top:6px;width:120px;height:34px;background:var(--yellow);font-family:"Oswald",sans-serif;font-size:18px;font-weight:500;display:flex;align-items:center;justify-content:center}
.room-grid{width:1000px;margin:26px auto 0;display:grid;grid-template-columns:repeat(3,310px);column-gap:35px;row-gap:40px}
.room-card{height:290px}
.room-photo{height:210px}
.room-photo.a{background:linear-gradient(#4a3a30,#1a1410)}
.room-photo.b{background:radial-gradient(ellipse at 50% 40%,#6a5a4e,#1e1914)}
.room-photo.c{background:linear-gradient(#3a3a3a,#0e0e0e)}
.room-photo.d{background:linear-gradient(#5a5650,#1e1c1a)}
.room-photo.e{background:linear-gradient(#6c6c6c,#2a2a2a)}
.room-photo.f{background:linear-gradient(#4d4d4d,#161616)}
.room-info{height:80px;background:var(--yellow);padding:10px 14px}
.room-info h3{font-family:"Oswald",sans-serif;font-size:15px;font-weight:500;line-height:18px}
.room-info p{font-size:10px;color:#4a3b00;margin:2px 0 6px}
.btn-small{display:inline-block;background:var(--white);font-family:"Oswald",sans-serif;font-size:9px;padding:3px 10px;letter-spacing:.5px}

.info-band{position:absolute;top:1940px;left:0;width:1200px;height:310px;background:var(--panel);padding-top:34px}
.info-band .wrap{display:flex;justify-content:space-between}
.info-col{width:300px}
.info-col h2{font-family:"Oswald",sans-serif;font-size:20px;font-weight:500;margin-bottom:16px}
.form-row{display:flex;gap:10px;margin-bottom:10px}
.field{background:var(--white);border:1px solid #ddd;height:28px;flex:1;font-size:10px;color:#999;padding:7px 8px}
.field.tall{height:80px}
.send{float:right;background:var(--dark);color:var(--white);font-family:"Oswald",sans-serif;font-size:10px;padding:6px 14px;margin-top:2px}
.contact-line{display:flex;gap:8px;align-items:flex-start;font-size:11px;color:#555;line-height:17px;margin-bottom:10px}
.contact-line svg{flex:none;margin-top:2px}
.map{height:170px;background:linear-gradient(135deg,#e6e4dc,#d7dcd2)}
.site-footer{position:absolute;top:2250px;left:0;width:1200px;height:218px;background:var(--darker);text-align:center;padding-top:26px}
.footer-nav{display:flex;justify-content:center;gap:20px;list-style:none;font-family:"Oswald",sans-serif;font-size:11px;color:#bdbdbd;letter-spacing:.5px}
.copyright{font-size:11px;color:#8a8a8a;margin:14px 0 18px}
.social{display:flex;justify-content:center;gap:10px}
.social i{width:26px;height:26px;border-radius:50%;display:block}
</style>
</head>
<body>

<header class="site-header">
  <div class="brand"><span class="brand-mark"></span><span class="brand-name">Puzzle Vaultery Des Moines</span></div>
</header>
<nav class="main-nav">
  <ul>
    <li class="active">Home</li><li>About Us</li><li>Who Should Try Puzzle Vaultery DM?</li><li>Rooms</li><li>Press Release</li><li>QRT Des Moines</li><li>Contact Us</li><li class="book">Book Now</li>
  </ul>
</nav>

<section class="hero">
  <div class="hero-media" role="img" aria-label="Slideshow photo of a lit escape room doorway with a video play button"></div>
  <div class="hero-arrow left"><svg width="14" height="24"><path d="M12 2 2 12l10 10" stroke="#ddd" stroke-width="2" fill="none"/></svg></div>
  <div class="hero-arrow right"><svg width="14" height="24"><path d="M2 2l10 10L2 22" stroke="#ddd" stroke-width="2" fill="none"/></svg></div>
</section>

<section class="welcome">
  <div class="wrap">
    <div class="welcome-text">
      <h1 class="section-title">Welcome to Puzzle Vaultery DM</h1>
      <p>Puzzle Vaultery DM is like nothing you have seen before. Located in the east side of downtown Des Moines, our live rooms put you and your team inside a story where every clue matters. Search the room, crack the codes and unlock the final door before the clock runs out. Each room has its own theme, puzzles and surprises.</p>
      <p>Challenge your friends, family or co-workers. Working together is the only way out. You have sixty minutes to find the hidden clues, solve the riddles and escape. Are you ready?</p>
      <div class="more">MORE ›</div>
    </div>
    <aside class="stat-box">
      <h3>CAN YOU ESCAPE IN 60 MIN?</h3>
      <div class="donuts">
        <div class="donut">
          <svg width="110" height="110" viewBox="0 0 110 110"><circle cx="55" cy="55" r="46" fill="none" stroke="#eee" stroke-width="10"/><circle cx="55" cy="55" r="46" fill="none" stroke="#e79a1f" stroke-width="10" stroke-dasharray="164.7 289" transform="rotate(-90 55 55)"/></svg>
          <span>57<small>Escaped</small></span>
        </div>
        <div class="donut">
          <svg width="110" height="110" viewBox="0 0 110 110"><circle cx="55" cy="55" r="46" fill="none" stroke="#eee" stroke-width="10"/><circle cx="55" cy="55" r="46" fill="none" stroke="#f8c21c" stroke-width="10" stroke-dasharray="124.3 289" transform="rotate(-90 55 55)"/></svg>
          <span>43<small>Failed</small></span>
        </div>
      </div>
    </aside>
  </div>
</section>

<div class="book-bar">BOOK NOW</div>

<section class="press">
  <div class="wrap">
    <div class="press-head"><h2 class="section-title">Press Release</h2><div class="press-nav"><i></i><i></i></div></div>
    <div class="press-list">
      <div class="press-item"><div class="date"><b>18</b><em>FEB</em></div><div><h4>You have 60 minutes, can you escape?</h4><p>Teams race the clock inside a locked room in Des Moines, a new kind of night out.</p></div></div>
      <div class="press-item"><div class="date"><b>18</b><em>FEB</em></div><div><h4>You have 60 minutes, can you escape?</h4><p>Teams race the clock inside a locked room in Des Moines, a new kind of night out.</p></div></div>
      <div class="press-item"><div class="date"><b>18</b><em>FEB</em></div><div><h4>You have 60 minutes, can you escape?</h4><p>Teams race the clock inside a locked room in Des Moines, a new kind of night out.</p></div></div>
      <div class="press-item"><div class="date"><b>18</b><em>FEB</em></div><div><h4>You have 60 minutes, can you escape?</h4><p>Teams race the clock inside a locked room in Des Moines, a new kind of night out.</p></div></div>
    </div>
  </div>
</section>

<div class="rooms-head"><span>ROOMS</span></div>
<div class="room-grid">
  <article class="room-card"><div class="room-photo a" role="img" aria-label="Room photo: warm dim interior"></div><div class="room-info"><h3>THE PARTY ROOM</h3><p>Min Players 5 | Max Players 12</p><span class="btn-small">BOOK NOW</span></div></article>
  <article class="room-card"><div class="room-photo b" role="img" aria-label="Room photo: dark moody scene"></div><div class="room-info"><h3>THE PARTY ROOM</h3><p>Min Players 5 | Max Players 12</p><span class="btn-small">BOOK NOW</span></div></article>
  <article class="room-card"><div class="room-photo c" role="img" aria-label="Room photo: shadowy doorway"></div><div class="room-info"><h3>THE PARTY ROOM</h3><p>Min Players 5 | Max Players 12</p><span class="btn-small">BOOK NOW</span></div></article>
  <article class="room-card"><div class="room-photo d" role="img" aria-label="Room poster: dark themed room artwork"></div><div class="room-info"><h3>THE PARTY ROOM</h3><p>Min Players 5 | Max Players 12</p><span class="btn-small">BOOK NOW</span></div></article>
  <article class="room-card"><div class="room-photo e" role="img" aria-label="Room poster: grey themed room artwork"></div><div class="room-info"><h3>THE PARTY ROOM</h3><p>Min Players 5 | Max Players 12</p><span class="btn-small">BOOK NOW</span></div></article>
  <article class="room-card"><div class="room-photo f" role="img" aria-label="Room poster: night themed room artwork"></div><div class="room-info"><h3>THE PARTY ROOM</h3><p>Min Players 5 | Max Players 12</p><span class="btn-small">BOOK NOW</span></div></article>
</div>

<section class="info-band">
  <div class="wrap">
    <div class="info-col">
      <h2>GET INVOLVED</h2>
      <div class="form-row"><div class="field">Name</div><div class="field">Email</div></div>
      <div class="form-row"><div class="field tall">Message</div></div>
      <span class="send">SEND</span>
    </div>
    <div class="info-col">
      <h2>CONTACT US</h2>
      <div class="contact-line">Contact: Dana Morrow</div>
      <div class="contact-line"><svg width="12" height="14" viewBox="0 0 12 14"><path d="M6 0a5 5 0 0 0-5 5c0 4 5 9 5 9s5-5 5-9a5 5 0 0 0-5-5z" fill="#555"/><circle cx="6" cy="5" r="2" fill="#f1f1f1"/></svg><span>Address: 214 Elm Row Ave,<br>Des Moines, IA</span></div>
      <div class="contact-line"><svg width="12" height="12" viewBox="0 0 12 12"><path d="M2 1h3l1 3-2 1a7 7 0 0 0 3 3l1-2 3 1v3c-6 0-9-3-9-9z" fill="#555"/></svg><span>Phone: 515-555-0142</span></div>
      <div class="contact-line"><svg width="12" height="12" viewBox="0 0 12 12"><path d="M2 1h3l1 3-2 1a7 7 0 0 0 3 3l1-2 3 1v3c-6 0-9-3-9-9z" fill="#555"/></svg><span>Alt Phone: 515-555-0187</span></div>
      <div class="contact-line"><svg width="12" height="10" viewBox="0 0 12 10"><rect x=".5" y=".5" width="11" height="9" fill="none" stroke="#555"/><path d="M.5.5 6 5l5.5-4.5" fill="none" stroke="#555"/></svg><span>Email: info@puzzlevaultery.com</span></div>
    </div>
    <div class="info-col">
      <h2>GET DIRECTIONS</h2>
      <div class="map" role="img" aria-label="Map of the Des Moines location"></div>
    </div>
  </div>
</section>

<footer class="site-footer">
  <ul class="footer-nav"><li>HOME</li><li>ABOUT US</li><li>WHO SHOULD TRY PUZZLE VAULTERY DM?</li><li>ROOMS</li><li>PRESS RELEASE</li><li>QRT DES MOINES</li><li>CONTACT US</li><li>BOOK NOW</li></ul>
  <p class="copyright">Copyright © 2015. Puzzle Vaultery DM</p>
  <div class="social"><i style="background:#3b5998"></i><i style="background:#1da1f2"></i><i style="background:#dd4b39"></i><i style="background:#cb2027"></i><i style="background:#e1306c"></i><i style="background:#0e76a8"></i><i style="background:#6aa84f"></i><i style="background:#f39c12"></i></div>
</footer>

</body>
</html>
```